Brindle Recycling needs a new web design

We need a new web design for our company based in Austin, TX. We resell and recycling electronics such as laptops, computer components, Zelvotabs, Quorns, etc. Since our inception over ten years ago, we’ve become one of the premier electronics recycling and remarketing companies in Austin, Texas.

```html
<!DOCTYPE html>
<html lang="en">
<head>
<meta charset="utf-8">
<title>Brindle Recycling</title>
<link rel="stylesheet" href="https://fonts.googleapis.com/css2?family=Marcellus&family=Roboto:wght@400;500;700&display=swap">
<style>
:root{
  --blue:#1c5db5;
  --blue-dark:#134a96;
  --green:#2b8a2c;
  --green-dark:#1f6f20;
  --ink:#222;
  --muted:#666;
  --light:#f1f3f5;
  --white:#fff;
  --cert-green:#dfeed3;
  --cert-paper:#f3f3f1;
}
*{box-sizing:border-box;margin:0;padding:0}
html,body{width:1200px;height:3939px;overflow:hidden}
body{position:relative;font-family:"Roboto",Arial,sans-serif;color:var(--ink);background:var(--white)}
.abs{position:absolute}
.serif{font-family:"Marcellus",Georgia,serif}
.btn{position:absolute;display:flex;align-items:center;justify-content:center;gap:8px;border-radius:30px;font-weight:700;font-size:15px;text-transform:uppercase;letter-spacing:.3px}
.btn-green{background:var(--green);color:var(--white)}
.btn-white{background:var(--white);color:var(--blue)}
.arrow-dot{width:14px;height:14px;border-radius:50%;background:currentColor;display:inline-flex}

.topbar{left:0;top:0;width:1200px;height:42px;background:var(--blue);color:var(--white);font-size:13px}
.topbar .contact{left:100px;top:13px;display:flex;gap:24px}
.topbar .quote{right:26px;top:0;width:229px;height:42px;background:var(--green);display:flex;align-items:center;justify-content:center;font-weight:500;font-size:14px;text-transform:uppercase}

.header{left:0;top:42px;width:1200px;height:121px;background:var(--white)}
.brand{left:100px;top:28px;display:flex;align-items:center;gap:12px}
.brand .mark{width:52px;height:52px;border-radius:50%;background:var(--blue)}
.brand .name{font-family:"Marcellus",Georgia,serif;font-size:30px;color:var(--blue-dark);line-height:1}
.nav{right:100px;top:50px;display:flex;gap:30px;font-size:15px;font-weight:500;text-transform:uppercase;color:#222}

.hero{left:0;top:163px;width:1200px;height:625px;background:radial-gradient(circle at 20% 20%,#7a2a22 0,#3a2a25 25%,#2a3428 55%,#151816 100%)}
.hero-title{left:0;top:190px;width:1200px;text-align:center;color:var(--white);font-size:40px;letter-spacing:1px;font-weight:400}
.hero-sub{left:300px;top:262px;width:600px;text-align:center;color:var(--white);font-size:19px;line-height:34px}
.hero .btn{left:508px;top:354px;width:170px;height:48px}
.hero-rule{left:340px;top:449px;width:520px;height:3px;background:var(--blue)}
.slide-arrow{top:230px;color:var(--white);font-size:26px}

.welcome{left:0;top:788px;width:1200px;height:420px;background:linear-gradient(#e9edf1,#fafbfc)}
.ghost{color:rgba(0,0,0,.06);font-family:"Marcellus",Georgia,serif;text-align:center;width:1200px;left:0;white-space:nowrap}
.welcome .ghost{top:88px;font-size:86px}
.welcome .kicker{left:0;top:108px;width:1200px;text-align:center;font-size:18px;color:#333}
.welcome .title{left:0;top:136px;width:1200px;text-align:center;font-size:36px;color:var(--blue);font-weight:400}
.welcome .text{left:220px;top:204px;width:760px;text-align:center;font-size:13px;line-height:27px;color:var(--muted)}
.welcome .btn{left:500px;top:330px;width:202px;height:50px;font-size:14px}

.split{left:0;top:1208px;width:1200px;height:500px}
.split .vert{top:260px;font-family:"Marcellus",Georgia,serif;font-size:70px;color:rgba(255,255,255,.13);transform:rotate(-90deg);width:460px;text-align:center}
.split .vert.right{transform:rotate(90deg)}
.split h3{font-family:"Marcellus",Georgia,serif;font-size:28px;color:var(--white);font-weight:400}
.split p{font-size:14px;line-height:27px;color:var(--white)}
.split .btn{width:158px;height:44px;font-size:14px}

.products{left:0;top:1707px;width:1200px;height:499px;background:var(--white)}
.products .ghost{top:30px;font-size:54px;color:rgba(28,93,181,.12)}
.products .title{left:0;top:36px;width:1200px;text-align:center;font-size:38px;color:var(--blue);font-weight:400}
.card{top:131px;width:234px;height:205px;background:var(--light)}
.card .pic{left:22px;top:14px;width:190px;height:140px;border-radius:4px}
.card .label{left:0;bottom:0;width:100%;height:46px;display:flex;align-items:center;justify-content:center;font-size:15px;font-weight:500;color:var(--blue);text-transform:uppercase}
.card.active .label{background:var(--blue);color:var(--white)}
.products .btn{left:480px;top:389px;width:238px;height:46px;font-size:15px}

.reviews{left:0;top:2206px;width:1200px;height:617px;background:linear-gradient(180deg,#2b2d33 0,#3d3d40 45%,#1f2229 100%)}
.reviews .ghost{top:114px;font-size:62px;color:rgba(255,255,255,.1)}
.reviews .title{left:0;top:116px;width:1200px;text-align:center;font-size:40px;color:var(--white);font-weight:400}
.quote-card{top:210px;width:308px;height:202px;background:var(--white)}
.quote-card .mark{left:0;top:14px;width:100%;text-align:center;font-size:56px;color:#cfcfcf;font-family:Georgia,serif;line-height:1}
.quote-card p{position:absolute;left:26px;top:66px;width:256px;text-align:center;font-size:13px;line-height:23px;color:#555}
.avatar{top:368px;width:86px;height:86px;border-radius:50%;border:4px solid var(--white);background:linear-gradient(#9aa7b3,#5b6570)}
.who{top:468px;width:308px;text-align:center;color:var(--white);font-size:14px}
.who b{font-size:15px}

.certs{left:0;top:2823px;width:1200px;height:565px;background:linear-gradient(#f6f7f8,#ffffff)}
.certs .ghost{top:40px;font-size:60px}
.certs .title{left:0;top:50px;width:1200px;text-align:center;font-size:38px;color:var(--blue);font-weight:400}
.certs .text{left:250px;top:124px;width:700px;text-align:center;font-size:14px;line-height:26px;color:var(--muted)}
.cert{top:205px;height:262px;background:var(--cert-green)}
.cert.doc{background:var(--cert-paper);border:1px solid #d8d8d8}

.contact{left:0;top:3388px;width:1200px;height:493px;background:linear-gradient(180deg,#1d61bd,#1a56a8)}
.contact .title{left:0;top:86px;width:1200px;text-align:center;font-size:36px;color:var(--white);font-weight:400}
.contact h4{font-size:16px;font-weight:700;color:var(--white);text-transform:uppercase}
.field{position:absolute;height:40px;border:1px solid rgba(255,255,255,.8);border-radius:8px;color:var(--white);font-size:14px;padding:10px 16px}
.contact .btn{left:157px;top:404px;width:108px;height:40px;font-size:14px;border-radius:20px}
.info{left:842px;color:var(--white);font-size:14px;line-height:24px}
.info .row{display:flex;align-items:center;gap:10px}
.socials{left:842px;top:404px;display:flex;gap:10px}
.socials span{width:34px;height:34px;border:2px solid var(--white);border-radius:50%}

.footer{left:0;top:3881px;width:1200px;height:58px;background:var(--green);color:var(--white);font-size:14px;font-weight:500;display:flex;align-items:center;justify-content:center;gap:16px}
</style>
</head>
<body>

<div class="abs topbar">
  <div class="abs contact">
    <span>&#9742;&nbsp; (512)555-0142</span><span>|</span><span>&#9993;&nbsp; hello@brindlerecycling.com</span>
  </div>
  <div class="abs quote">Request a Qoute</div>
</div>

<header class="abs header">
  <div class="abs brand"><span class="mark"></span><span class="name">Brindle Recycling</span></div>
  <nav class="abs nav">
    <span>Home</span><span>About Us</span><span>Services</span><span>Products</span><span>Blog</span><span>Contact Us</span>
    <svg width="16" height="16" viewBox="0 0 16 16"><circle cx="6.5" cy="6.5" r="5" fill="none" stroke="#222" stroke-width="2"/><path d="M10.5 10.5 15 15" stroke="#222" stroke-width="2"/></svg>
  </nav>
</header>

<section class="abs hero" role="img" aria-label="Close-up of hands in work gloves sorting circuit boards and cables">
  <div class="abs slide-arrow" style="left:40px">&#8249;</div>
  <div class="abs slide-arrow" style="right:40px">&#8250;</div>
  <h1 class="abs hero-title serif">BRINDLE RECYCLING</h1>
  <p class="abs hero-sub">To achieve a “Zero Landfill Policy” through the effective management of safety, health, environment and community issues.</p>
  <div class="btn btn-green">Read More <span class="arrow-dot"></span></div>
  <div class="abs hero-rule"></div>
</section>
<svg class="abs" style="left:0;top:650px" width="1200" height="140" viewBox="0 0 1200 140">
  <polygon points="0,20 600,138 1200,20 1200,140 0,140" fill="#e9edf1"/>
  <polyline points="0,20 600,138 1200,20" fill="none" stroke="#1c5db5" stroke-width="6"/>
  <polyline points="585,44 600,56 615,44" fill="none" stroke="#fff" stroke-width="3"/>
  <polyline points="585,56 600,68 615,56" fill="none" stroke="#fff" stroke-width="3"/>
</svg>

<section class="abs welcome">
  <div class="abs ghost">ABOUT US</div>
  <div class="abs kicker serif">WELCOME TO</div>
  <h2 class="abs title serif">BRINDLE RECYCLING</h2>
  <p class="abs text">At Brindle Recycling, we’re committed to providing environmentally friendly recycling solutions to Austin and the surrounding areas. Founded in 2006, our mission is to process your materials in a safe, non-hazardous manner — with an aim to keep the world environmentally clean. As a R2 recycling center, we believe in promoting smart recycling habits in order to achieve long lasting results.</p>
  <div class="btn btn-green">Schedule a Pickup</div>
</section>

<section class="abs split">
  <svg class="abs" style="left:0;top:0" width="1200" height="500" viewBox="0 0 1200 500">
    <polygon points="0,0 600,70 600,500 0,452" fill="#1c5db5"/>
    <polygon points="600,70 1200,0 1200,452 600,500" fill="#2b8a2c"/>
  </svg>
  <div class="abs vert" style="left:-205px">RECYCLING</div>
  <div class="abs vert right" style="left:945px">RESELLING</div>
  <h3 class="abs" style="left:100px;top:120px">RECYCLING</h3>
  <p class="abs" style="left:100px;top:174px;width:400px">At Brindle Recycling, we strive to keep the environment clean through our wide range of services. Our E-Waste Recycling services were designed to simplify the recycling process for residents in the Austin area. Contact us today and see how you can contribute to making this world a cleaner place.</p>
  <div class="btn btn-white" style="left:100px;top:328px">Read More <span class="arrow-dot"></span></div>
  <h3 class="abs" style="left:701px;top:120px">RESELLING</h3>
  <p class="abs" style="left:701px;top:174px;width:400px">At Brindle Recycling, we go out of our way to make sure your recycling process is made easy as possible. Our Recycling Pickup service is designed to simplify all of your recycling needs. Take a look at all the services we offer and get in touch to see how you can start the process today!</p>
  <div class="btn btn-white" style="left:701px;top:328px;color:var(--green)">Read More <span class="arrow-dot"></span></div>
</section>

<section class="abs products">
  <div class="abs ghost">RECYCLING PRODUCTS</div>
  <h2 class="abs title serif">RECYCLING PRODUCTS</h2>
  <div class="abs card" style="left:100px"><div class="abs pic" role="img" aria-label="Open laptop" style="background:linear-gradient(#c9d2dc,#8c96a2)"></div><div class="abs label">Laptops</div></div>
  <div class="abs card active" style="left:355px"><div class="abs pic" role="img" aria-label="Desktop computer with monitor and tower" style="background:linear-gradient(#cfe0f2,#5e6670)"></div><div class="abs label">Computer Component</div></div>
  <div class="abs card" style="left:612px"><div class="abs pic" role="img" aria-label="Tablet on a stand" style="background:linear-gradient(#3b3f44,#1b1d20)"></div><div class="abs label">Zelvotabs</div></div>
  <div class="abs card" style="left:869px"><div class="abs pic" role="img" aria-label="Silver notebook computer" style="background:linear-gradient(#b07acb,#4c3a6e)"></div><div class="abs label">Quorns</div></div>
  <div class="btn btn-green">View All Products <span class="arrow-dot"></span></div>
</section>

<section class="abs reviews" role="img" aria-label="City skyline at dusk behind client testimonials">
  <svg class="abs" style="left:0;top:0" width="1200" height="30" viewBox="0 0 1200 30"><polygon points="0,0 1200,0 1200,4 600,26 0,4" fill="#fff"/></svg>
  <div class="abs ghost">TESTIMONIALS</div>
  <h2 class="abs title serif">WHAT OUR CLIENTS SAY</h2>
  <div class="abs quote-card" style="left:100px"><div class="abs mark">&ldquo;</div><p>"At vero eos et accusamus et iusto odio dignissimos ducimus qui blanditiis tatum delgd emlt atque corrupti quos dolores et quas ex ffe ghr molestias"</p></div>
  <div class="abs quote-card" style="left:446px"><div class="abs mark">&ldquo;</div><p>"At vero eos et accusamus et iusto odio dignissimos ducimus qui blanditiis tatum delgd emlt atque corrupti quos dolores et quas ex ffe ghr molestias"</p></div>
  <div class="abs quote-card" style="left:793px"><div class="abs mark">&ldquo;</div><p>"At vero eos et accusamus et iusto odio dignissimos ducimus qui blanditiis tatum delgd emlt atque corrupti quos dolores et quas ex ffe ghr molestias"</p></div>
  <div class="abs avatar" style="left:211px"></div>
  <div class="abs avatar" style="left:557px"></div>
  <div class="abs avatar" style="left:904px"></div>
  <div class="abs who" style="left:100px"><b>ARJUN MEHRA</b>, Creative Manager</div>
  <div class="abs who" style="left:446px"><b>LENA PRUITT</b>, Creative Manager</div>
  <div class="abs who" style="left:793px"><b>MARC TOLVER</b>, Creative Manager</div>
</section>

<section class="abs certs">
  <div class="abs ghost">CERTIFICATION</div>
  <h2 class="abs title serif">OUR CERTIFICATION</h2>
  <p class="abs text">At vero eos et accusamus et iusto odio dignissimos ducimus qui blanditiis praesentium voluptatum deleniti atque corrupti quos dolores et quas molestias excepturi sint occaecati cupiditate non provident</p>
  <div class="abs cert" style="left:100px;width:194px" role="img" aria-label="Scanned certificate of certification"></div>
  <div class="abs cert" style="left:318px;width:197px" role="img" aria-label="Scanned certificate of certification"></div>
  <div class="abs cert" style="left:536px;width:197px" role="img" aria-label="Scanned certificate of certification"></div>
  <div class="abs cert doc" style="left:759px;width:341px" role="img" aria-label="Scanned state environmental registration letter"></div>
</section>

<section class="abs contact">
  <svg class="abs" style="left:0;top:-60px" width="1200" height="70" viewBox="0 0 1200 70">
    <polygon points="0,70 600,0 1200,70" fill="#2b8a2c"/>
    <polygon points="0,70 600,16 1200,70" fill="#1d61bd"/>
  </svg>
  <h2 class="abs title serif">CONTACT US</h2>
  <h4 class="abs" style="left:157px;top:168px">Get in Touch</h4>
  <div class="field" style="left:157px;top:215px;width:275px">Name</div>
  <div class="field" style="left:449px;top:215px;width:275px">Phone</div>
  <div class="field" style="left:157px;top:265px;width:567px">Email</div>
  <div class="field" style="left:157px;top:315px;width:567px;height:68px">Message</div>
  <div class="btn btn-green">Submit</div>

  <div class="abs info" style="top:166px"><h4>Address:</h4>
    <div class="row"><svg width="12" height="16" viewBox="0 0 12 16"><path d="M6 0a6 6 0 0 0-6 6c0 4.5 6 10 6 10s6-5.5 6-10a6 6 0 0 0-6-6zm0 8.5A2.5 2.5 0 1 1 6 3.5a2.5 2.5 0 0 1 0 5z" fill="#fff"/></svg>4120 Pecan Ridge Dr.</div>
    <div style="padding-left:22px">Austin, Texas 78799</div>
  </div>
  <div class="abs info" style="top:248px"><h4>Phone:</h4>
    <div class="row"><svg width="14" height="14" viewBox="0 0 14 14"><path d="M3 0l2.5 3.5-1.5 2a8 8 0 0 0 4.5 4.5l2-1.5L14 11l-2 3C5.5 14 0 8.5 0 2z" fill="#fff"/></svg>(512)555-0142</div>
    <div class="row"><svg width="14" height="14" viewBox="0 0 14 14"><rect x="1" y="3" width="12" height="9" rx="1" fill="#fff"/><rect x="3" y="0" width="8" height="4" fill="#fff"/></svg>(512)555-0198</div>
  </div>
  <div class="abs info" style="top:338px"><h4>Email:</h4>
    <div class="row"><svg width="14" height="11" viewBox="0 0 14 11"><rect width="14" height="11" fill="#fff"/><path d="M0 0l7 6 7-6" fill="none" stroke="#1c5db5" stroke-width="1.5"/></svg>hello@brindlerecycling.com</div>
  </div>
  <div class="abs socials"><span></span><span></span><span></span><span></span></div>
</section>

<footer class="abs footer"><span>&copy; Copyright 2018 Brindle Recycling. All Rights Reserved</span><span>|</span><span>Privacy Policy.</span></footer>

</body>
</html>
```